Retro Label for old fashioned soda

We need a label for soda we are having private labeled for our retro, 1950's ice cream shop www.maplefrostparlor.example I don't want the label to look like something from 2017 with a retro feel, but more like an original (possibly kinda cheesy) label you'd see from the 1950's with some of the old catch lines like "tastes great", "invigorating" or "it is refreshing!" The prominent brand should be the name of our ice cream shop, Maple Frost Parlor. the soda is also pure cane sugar so it might be good to have that on somewhere

Label size is 2.4" wide by 4" tall. Here is an example of some retro labels from findwell. I attached on file to this contest but there are more here: https://www.findwell.example/images?q=retro+soda+label&ref=Kx7Qm2Lp9Vt4Rz8Nw3Hd5Jb6Yc1Fg0TsUaWe2Pv7Xo4Ml9Qn8Bk3Dr6Zh5Cy1Ej0Gu7Ai4Ot2Sf9Lw6Nx8Mb3&w=2560&h=1470#img=Pq7Rt2Vw9Xz4Ab:

The label will be the same for all the flavors with the exception of the flavor name changing somewhere on the label. These are the flavors

Root Beer
Orange
Black Cherry
Lemonade
Raspberry Lime -Rickey
White Birch Beer
Lemon Iced Tea
Vanilla Cream
Orange Cream
Sarsaparilla
Ginger Ale

Industry/Entity Type

Shop

Colors

Designer to choose colors to be used in the design.

Requirements
Must have
• retro feel. authentic old fashioned look

```html
<!DOCTYPE html>
<html lang="en">
<head>
<meta charset="utf-8">
<title>Maple Frost Parlor – Black Cherry Soda Label</title>
<link rel="stylesheet" href="https://fonts.googleapis.com/css2?family=Oswald:wght@600&family=Lobster&family=Bitter:wght@700&family=Old+Standard+TT&display=swap">
<style>
  :root {
    --backdrop: #dfe5e7;
    --label-cream: #d8c79c;
    --label-ray: #bfa97a;
    --shield-edge: #1f3b3c;
    --shield-teal: #3f7a72;
    --shield-red: #b3343a;
    --shield-rule: #e6d9b4;
    --night: #1e2a38;
    --gold: #e2b23c;
    --cream-type: #f2e6c2;
    --script-red: #e0474d;
    --ink: #2a2420;
  }
  html, body {
    margin: 0;
    width: 1200px;
    height: 901px;
    overflow: hidden;
    background: var(--backdrop);
  }
  .label {
    position: absolute;
    left: 355px;
    top: 40px;
    width: 490px;
    height: 820px;
    box-shadow: 0 6px 18px rgba(0,0,0,.18);
  }
  .banner-text { font-family: "Oswald", sans-serif; font-weight: 600; font-size: 30px; fill: var(--gold); letter-spacing: 1px; }
  .brand-name { font-family: "Bitter", serif; font-weight: 700; font-size: 48px; fill: var(--cream-type); text-anchor: middle; }
  .flavor-name { font-family: "Bitter", serif; font-weight: 700; font-size: 30px; fill: var(--ink); text-anchor: middle; }
  .sugar-line { font-family: "Lobster", cursive; font-size: 30px; fill: var(--script-red); text-anchor: middle; }
  .volume { font-family: "Old Standard TT", serif; font-size: 26px; fill: var(--ink); }
</style>
</head>
<body>
<svg class="label" viewBox="0 0 490 820" xmlns="http://www.w3.org/2000/svg">
  <defs>
    <radialGradient id="rayGlow" cx="50%" cy="45%" r="70%">
      <stop offset="0" stop-color="#d8c79c"/>
      <stop offset="1" stop-color="#bfa97a"/>
    </radialGradient>
    <clipPath id="shieldClip">
      <polygon points="245,40 440,130 440,610 245,755 50,610 50,130"/>
    </clipPath>
  </defs>

  <rect class="label-ground" width="490" height="820" fill="url(#rayGlow)" role="img" aria-label="Cream sunburst rays radiating behind the shield"/>

  <g class="shield">
    <polygon points="245,22 458,122 458,618 245,775 32,618 32,122" fill="var(--shield-edge)"/>
    <polygon points="245,40 440,130 440,610 245,755 50,610 50,130" fill="var(--shield-teal)"/>
    <rect x="40" y="30" width="410" height="190" fill="var(--shield-red)" clip-path="url(#shieldClip)"/>
    <polygon points="245,56 424,140 424,600 245,736 66,600 66,140" fill="none" stroke="var(--shield-rule)" stroke-width="3"/>
  </g>

  <g class="slogan-banner">
    <path d="M 60 258 Q 240 214 430 146" fill="none" stroke="var(--night)" stroke-width="46"/>
    <path id="sloganArc" d="M 78 266 Q 240 224 420 160" fill="none"/>
    <text class="banner-text"><textPath href="#sloganArc" startOffset="50%" text-anchor="middle">QUENCH YOUR THIRST</textPath></text>
  </g>

  <ellipse class="title-plate" cx="245" cy="395" rx="205" ry="92" fill="var(--night)"/>

  <text class="brand-name" x="245" y="384">Maple Frost</text>
  <text class="brand-name" x="245" y="440">Parlor</text>

  <g class="flavor-banner">
    <polygon points="100,488 390,488 404,518 390,548 100,548 86,518" fill="var(--gold)" stroke="var(--night)" stroke-width="3"/>
    <text class="flavor-name" x="245" y="529">Black Cherry</text>
  </g>

  <text class="sugar-line" x="245" y="602">Made from Pure</text>
  <text class="sugar-line" x="245" y="638">Cane Sugar</text>

  <text class="volume" x="22" y="700">16oz</text>
  <text class="volume" x="468" y="700" text-anchor="end">500ml</text>
</svg>
</body>
</html>
```